Stylish Business Cards Wanted

- DOUBLE SIDED Design Required -

High end, edgy cards for a corporate and personal stylist. Must include logo,
Name: Belinda Harwick
Title: Director and Stylist
telephone : +61 8 7142 5809
email: belinda@theloombriefing.example
website: theloombriefing.example
Tag: Corporate Workwear & Uniform Specialist | Personal Stylist
Would like nice icons for telephone, email, website

Target Market(s)

Businesses wanting stylish uniforms, people wanting stylish wardrobes

Industry/Entity Type

Corporate Workwear Stylist

Contact Information for Business Card

I would like black, white and gold foiling incorporated in the design - possibly a touch of the other colours on my branding guide attached Name: Belinda Harwick Title: Director and Stylist telephone : +61 8 7142 5809 email: belinda@theloombriefing.example website: theloombriefing.example Tag: Corporate Workwear & Uniform Specialist | Personal Stylist Would like nice icons for telephone, email, website

Font styles to use
Other font styles liked:
• Raleway

Colors

Designer to choose colors to be used in the design.

Requirements
Must have
• Gold foil accents

```html
<!DOCTYPE html>
<html lang="en">
<head>
<meta charset="utf-8">
<title>The Loom Briefing – Business Card</title>
<link rel="stylesheet" href="https://fonts.googleapis.com/css2?family=Cinzel:wght@700&family=Open+Sans:wght@400;600&display=swap">
<style>
  :root {
    --canvas: #e8e6e3;
    --paper: #ffffff;
    --charcoal: #333333;
    --gold: #e3bf5e;
    --ink-light: #ffffff;
  }
  * { margin: 0; padding: 0; box-sizing: border-box; }
  html, body {
    width: 1200px; height: 900px; overflow: hidden;
    background: var(--canvas);
  }
  .card {
    position: absolute; left: 100px; top: 139px;
    width: 1000px; height: 622px;
    background: var(--paper);
    box-shadow: 0 10px 30px rgba(0,0,0,0.18);
    overflow: hidden;
    font-family: "Open Sans", Arial, sans-serif;
  }
  .card__bands { position: absolute; inset: 0; }
  .brand {
    position: absolute; left: 0; right: 0; top: 130px;
    text-align: center;
    font-family: "Open Sans", Arial, sans-serif;
    font-weight: 600; font-size: 56px; letter-spacing: 1px;
    color: var(--charcoal);
  }
  .contact-list {
    position: absolute; left: 37px; top: 428px;
    list-style: none;
  }
  .contact-list__item {
    display: flex; align-items: center;
    height: 38px;
    color: var(--ink-light); font-size: 20px;
  }
  .contact-list__icon { width: 30px; height: 30px; margin-right: 16px; flex: none; }
  .person {
    position: absolute; right: 81px; top: 384px;
    text-align: right;
  }
  .person__name {
    font-family: "Cinzel", Georgia, serif; font-weight: 700;
    font-size: 30px; line-height: 1; color: var(--gold); letter-spacing: 0.5px;
  }
  .person__title { font-size: 16px; color: var(--ink-light); margin-top: 2px; }
  .tagline {
    position: absolute; left: 669px; top: 478px;
    color: var(--ink-light); font-size: 20px; line-height: 30px;
  }
</style>
</head>
<body>
  <div class="card">
    <svg class="card__bands" width="1000" height="622" viewBox="0 0 1000 622">
      <polygon points="0,325 546,325 513,363 0,363" fill="var(--gold)"/>
      <polygon points="0,369 519,369 562,318 1000,320 1000,622 0,622" fill="var(--charcoal)"/>
    </svg>

    <div class="brand">The Loom Briefing</div>

    <ul class="contact-list">
      <li class="contact-list__item">
        <svg class="contact-list__icon" viewBox="0 0 30 30">
          <rect width="30" height="30" rx="6" fill="var(--gold)"/>
          <path d="M9 7c1.2-.8 2.2-.6 2.8.4l1.5 2.6c.5.9.2 1.7-.6 2.3l-.9.7c.9 2.2 2.5 3.9 4.6 5l.8-.9c.6-.8 1.5-1 2.3-.5l2.6 1.5c1 .6 1.1 1.7.3 2.7-1.3 1.6-3 2.3-5 1.6C12 20.6 8.6 17 7.4 12.3 6.9 10.2 7.5 8.2 9 7z" fill="var(--charcoal)"/>
        </svg>
        +61 8 7142 5809
      </li>
      <li class="contact-list__item">
        <svg class="contact-list__icon" viewBox="0 0 30 30">
          <rect width="30" height="30" rx="6" fill="var(--gold)"/>
          <rect x="10" y="6" width="10" height="6" fill="none" stroke="var(--charcoal)" stroke-width="1.8"/>
          <rect x="6" y="11" width="18" height="9" rx="1.5" fill="var(--charcoal)"/>
          <rect x="10" y="17" width="10" height="8" fill="var(--gold)" stroke="var(--charcoal)" stroke-width="1.8"/>
          <path d="M12 20h6M12 22.5h6" stroke="var(--charcoal)" stroke-width="1.2"/>
        </svg>
        +61 8 7142 5810
      </li>
      <li class="contact-list__item">
        <svg class="contact-list__icon" viewBox="0 0 30 30">
          <rect x="2" y="6" width="26" height="18" rx="2" fill="none" stroke="var(--gold)" stroke-width="2"/>
          <path d="M3 7l12 10L27 7M3 23l9-8M27 23l-9-8" fill="none" stroke="var(--gold)" stroke-width="2"/>
        </svg>
        belinda@theloombriefing.example
      </li>
      <li class="contact-list__item">
        <svg class="contact-list__icon" viewBox="0 0 30 30">
          <rect width="30" height="30" rx="6" fill="var(--gold)"/>
          <g fill="none" stroke="var(--charcoal)" stroke-width="1.6">
            <circle cx="15" cy="15" r="9"/>
            <ellipse cx="15" cy="15" rx="4" ry="9"/>
            <path d="M6 15h18M7.5 10.5h15M7.5 19.5h15"/>
          </g>
        </svg>
        theloombriefing.example
      </li>
    </ul>

    <div class="person">
      <div class="person__name">BELINDA HARWICK</div>
      <div class="person__title">Director and Stylist</div>
    </div>

    <div class="tagline">
      Corporate Workwear &amp;<br>
      Uniform Specialist<br>
      Personal Stylist
    </div>
  </div>
</body>
</html>
```